A Modern & Sleek "Coming Soon" Page for an A.I Recruiting App

For the “Coming Soon” website, a simple background with no people in it. I've attached an A.I image of what the page should generally look like.

- A single mobile phone as the main focus where the user actually clicks on the, “notify me” button (after entering their email address).
- In the background where the pillars/columns are seen in the example, should be subtle pad locks that are in their opened position with a key inside the lock. I've attached images to try to illustrate this idea, but they are far away in style from what I'm looking for.

SLOGAN: Unlocking the power of meaningful connections
LOGO/TITLE: Should be the name as shown in image with only the name "KelvoLink" on it
COLORS: Purplish/blue hues. Should not be too feminine
NOTE: The user should only click once when signing up/entering their email.

Product: A recruiting platform that matches employers/employees with A.I. and prioritizing cultural fit/values system before skills. The industry we are tackling first is the caregiving industry (nannies, tutors, elderly). All users will be background screened and that info lives on the blockchain. All users will have the option to review and be reviewed/rated.

```html
<!DOCTYPE html>
<html lang="en">
<head>
<meta charset="UTF-8">
<title>KelvoLink — Coming Soon</title>
<link rel="stylesheet" href="https://fonts.googleapis.com/css2?family=Orbitron:wght@400;500&family=Poppins:wght@600&display=swap">
<style>
  :root {
    --bg-base: #6230c4;
    --bg-deep: #5522b8;
    --bg-glow: #7a46d2;
    --heart-tint: rgba(200, 70, 190, 0.35);
    --phone-rim: #7fb4e6;
    --phone-body: #1a1a24;
    --screen-top: #8c2c86;
    --screen-bottom: #4410a8;
    --accent: #dc36a4;
    --text-light: #ffffff;
    --text-soft: #d9ccf5;
    --lock-steel: #55525e;
    --lock-dark: #2f2d36;
    --lock-glow: #46e07a;
  }
  * { margin: 0; padding: 0; box-sizing: border-box; }
  html, body { width: 1200px; height: 598px; overflow: hidden; }
  body {
    position: relative;
    background:
      radial-gradient(circle at 12% 12%, var(--heart-tint) 0, transparent 9%),
      radial-gradient(circle at 55% 14%, var(--heart-tint) 0, transparent 10%),
      radial-gradient(circle at 65% 80%, var(--heart-tint) 0, transparent 11%),
      radial-gradient(circle at 5% 92%, var(--heart-tint) 0, transparent 9%),
      radial-gradient(circle at 45% 45%, var(--bg-glow) 0, transparent 45%),
      linear-gradient(180deg, var(--bg-base), var(--bg-deep));
    font-family: "Orbitron", sans-serif;
    color: var(--text-light);
  }
  .phone {
    position: absolute;
    left: 92px; top: 62px;
    width: 255px; height: 504px;
    border-radius: 38px;
    background: var(--phone-body);
    border: 3px solid var(--phone-rim);
    padding: 8px;
  }
  .phone-screen {
    position: relative;
    width: 100%; height: 100%;
    border-radius: 30px;
    background: linear-gradient(180deg, var(--screen-top) 0%, var(--screen-bottom) 38%, var(--screen-bottom) 100%);
    text-align: center;
    overflow: hidden;
  }
  .phone-notch {
    position: absolute;
    top: 0; left: 50%;
    transform: translateX(-50%);
    width: 106px; height: 20px;
    background: var(--phone-body);
    border-radius: 0 0 14px 14px;
  }
  .brand-name {
    position: absolute;
    top: 132px; left: 0; right: 0;
    font-size: 23px;
    font-weight: 400;
    letter-spacing: 2px;
    text-transform: uppercase;
  }
  .phone-slogan {
    position: absolute;
    top: 210px; left: 0; right: 0;
    font-size: 11.5px;
    font-weight: 500;
    line-height: 26px;
    text-transform: uppercase;
  }
  .button {
    display: flex;
    align-items: center;
    justify-content: center;
    background: var(--accent);
    color: var(--text-light);
    font-family: "Poppins", sans-serif;
    font-weight: 600;
    text-transform: uppercase;
    border-radius: 999px;
    border: none;
  }
  .notify-button {
    position: absolute;
    top: 324px; left: 46px;
    width: 149px; height: 41px;
    font-size: 13px;
  }
  .phone-note {
    position: absolute;
    top: 420px; left: 0; right: 0;
    font-size: 9px;
    line-height: 15px;
    color: var(--text-soft);
  }
  .hero {
    position: absolute;
    left: 400px; top: 184px;
  }
  .hero-title {
    font-size: 29px;
    font-weight: 500;
    line-height: 52px;
    text-transform: uppercase;
    letter-spacing: 1px;
  }
  .signup-button {
    margin-top: 16px;
    width: 168px; height: 47px;
    font-size: 15px;
  }
  .padlock-art {
    position: absolute;
    left: 836px; top: 86px;
    width: 350px; height: 463px;
    border-radius: 40px;
    background:
      radial-gradient(circle at 33% 70%, rgba(70, 224, 122, 0.55) 0, transparent 18%),
      linear-gradient(160deg, var(--lock-steel), var(--lock-dark));
    opacity: 0.9;
  }
</style>
</head>
<body>
  <div class="phone">
    <div class="phone-screen">
      <div class="phone-notch"></div>
      <div class="brand-name">KelvoLink</div>
      <p class="phone-slogan">Unlocking the<br>power of meaningful<br>connections</p>
      <button class="button notify-button">Notify me</button>
      <p class="phone-note">Early access coming soon<br>&amp; updates first</p>
    </div>
  </div>

  <section class="hero">
    <h1 class="hero-title">Unlocking the<br>power of meaningful<br>connections</h1>
    <button class="button signup-button">Sign up</button>
  </section>

  <div class="padlock-art" role="img" aria-label="Open steel padlock with a key in its glowing green keyhole"></div>
</body>
</html>
```